Smart, Classy, Conservative looking Legal Letterhead

I need a letterhead that when you look at it it "says to you " this is a well established law firm with very smart lawyers, which will one day be appearing before the Supreme Court of the USA. All information about the Law firm should appear at the top of the page. please no information in the footer.

Industry/Entity Type

Legal

Requirements
Must have
• The name of the law firm, both addresses, phone number and fax,, The names of the attorneys, the website.
• Fields that get changed such as the date, VIA, Address of who the letter is going to,
• Re, Index,
• should have a clean neat look, sleek
Nice to have
• some color would be nice. A logo of some sort could be nice as well. Maybe a single S or interlocking M's For Merriton and Merriton.
Should not have
• not too modern looking.

```html
<!DOCTYPE html>
<html lang="en">
<head>
<meta charset="utf-8">
<title>Merriton &amp; Merriton, LLC — Letterhead</title>
<link rel="stylesheet" href="https://fonts.googleapis.com/css2?family=Cinzel:wght@400;500&family=Didact+Gothic&display=swap">
<style>
  :root {
    --backdrop: #1e1e1e;
    --paper: #f1f1f1;
    --brand-blue: #0f5b80;
    --band-grey: #9a9a9a;
    --ink: #2b2b2b;
    --ink-soft: #444;
  }
  html, body { margin: 0; padding: 0; }
  body {
    width: 1200px; height: 1000px; overflow: hidden;
    background: var(--backdrop);
    position: relative;
  }
  .letterhead {
    position: absolute; left: 256px; top: 53px;
    width: 689px; height: 892px;
    background: var(--paper);
    font-family: "Didact Gothic", "Century Gothic", sans-serif;
    color: var(--ink-soft);
  }
  .band { position: absolute; top: 0; height: 11px; }
  .band--primary { left: 0; width: 424px; background: var(--brand-blue); }
  .band--secondary { left: 430px; width: 259px; background: var(--band-grey); }

  .firm-mark {
    position: absolute; left: 40px; top: 49px;
    width: 32px; height: 32px; background: var(--brand-blue);
  }
  .firm-name {
    position: absolute; left: 100px; top: 45px;
    font-family: "Cinzel", "Trajan Pro", serif;
    color: var(--ink);
  }
  .firm-name__title {
    margin: 0; font-size: 17px; font-weight: 400; letter-spacing: 0.2px;
    padding-bottom: 3px; border-bottom: 1px solid var(--ink);
    width: 266px; white-space: nowrap;
  }
  .firm-name__tagline {
    margin: 3px 0 0; font-size: 12px; letter-spacing: 0.3px;
  }

  .attorneys {
    position: absolute; left: 42px; top: 108px;
    margin: 0; padding: 0; list-style: none;
    font-size: 8px; line-height: 11px; text-transform: uppercase;
  }
  .attorneys .note { font-size: 6.5px; line-height: 9px; }

  .contact {
    position: absolute; right: 39px; top: 47px;
    text-align: right; font-size: 8px; line-height: 9.8px;
  }
  .contact p { margin: 0; }
  .contact .label { color: var(--brand-blue); font-weight: 700; }
  .office-heading {
    margin-top: 14px !important;
    color: var(--brand-blue); font-weight: 700; text-transform: uppercase;
  }
</style>
</head>
<body>
  <main class="letterhead">
    <div class="band band--primary"></div>
    <div class="band band--secondary"></div>

    <div class="firm-mark" aria-hidden="true"></div>
    <header class="firm-name">
      <h1 class="firm-name__title">Merriton &amp; Merriton, LLC</h1>
      <p class="firm-name__tagline">Attorneys at Law</p>
    </header>

    <ul class="attorneys">
      <li>Michael Merriton, Esq.</li>
      <li>Daniel A. Merriton, Esq.</li>
      <li>Elizabeth Hartwell, Esq.</li>
      <li>Peter T. Dorsey, Esq.*</li>
      <li class="note">*Admitted in NY &amp; MA</li>
    </ul>

    <address class="contact" style="font-style:normal">
      <p>118 Fulton Street</p>
      <p>New York, New York 10038</p>
      <p><span class="label">Tel:</span> 914-555-0142 · <span class="label">Fax:</span> 914-555-0178</p>
      <p><span class="label">Email:</span> Daniel.Merriton@merritonlegal.com</p>
      <p>www.nyconsumerdefense.com</p>
      <p class="office-heading">Westchester Office</p>
      <p>217 Linden Road</p>
      <p>Pleasantville</p>
      <p>New York 10570</p>
    </address>
  </main>
</body>
</html>
```